Stationery Design Project

I need a stationary design for our company. we are based in Houston, TX and we are called Mira Vell Lending. And we are wanting to brand our MoneyMendPlus program, which includes our tax preparation and restoration, credit repair service. Although our business offers other programs, we are interested in mainly focusing on The MoneyMendPlus program. We are looking for way to brand our ourselves and I believe that a great stationery design will help in achieving this goal. Our logo design is blue and light blue. the slogan is orange.

Industry/Entity Type

Business

Requirements
Must have
• Address: 30871 Calloway Ln. B-22
Houston, TX 75419
Tel. 555-318-6207
Fax 555-294-7153
www.miravelllending.example
info@miravelllending.example
Our Slogan: Happiness, Restored!

```html
<!DOCTYPE html>
<html lang="en">
<head>
<meta charset="utf-8">
<title>MoneyMendPlus Business Card</title>
<link href="https://fonts.googleapis.com/css2?family=Tinos:wght@400;700&display=swap" rel="stylesheet">
<style>
  :root {
    --backdrop: #e8e5e0;
    --paper: #ffffff;
    --navy: #143f68;
    --blue: #1f5f99;
    --sky: #1d8fd0;
    --orange: #f0922a;
    --ink: #2a2a2a;
    --frame: #9fb8d4;
  }
  * { margin: 0; padding: 0; box-sizing: border-box; }
  html, body {
    width: 1200px; height: 977px; overflow: hidden;
    background: var(--backdrop);
    font-family: "Tinos", "Times New Roman", serif;
  }
  .stage { position: relative; width: 1200px; height: 977px; }

  .card { position: absolute; width: 730px; height: 417px; overflow: hidden; box-shadow: 0 2px 6px rgba(0,0,0,.25); }
  .card-front { left: 60px; top: 50px; background: var(--paper); }
  .card-back { left: 387px; top: 508px; background: var(--navy); }

  .front-waves { position: absolute; inset: 0; }

  .program-name {
    position: absolute; left: 48px; top: 128px;
    font-size: 54px; font-weight: 400; color: var(--blue); letter-spacing: -0.5px;
  }
  .slogan {
    position: absolute; left: 72px; top: 196px;
    font-size: 25px; font-weight: 700; color: var(--orange); letter-spacing: 2px;
  }
  .address {
    position: absolute; left: 76px; top: 268px;
    font-size: 19px; line-height: 27px; color: var(--ink);
  }
  .contact {
    position: absolute; right: 30px; top: 286px;
    list-style: none; text-align: right; color: #fff; font-size: 19px;
  }
  .contact li { height: 29px; display: flex; align-items: center; justify-content: flex-end; gap: 8px; }
  .contact svg { width: 15px; height: 15px; fill: #fff; }

  .company-badge {
    position: absolute; left: 568px; top: 22px; width: 132px; height: 132px;
    background: var(--navy); border: 3px solid var(--frame);
    display: flex; align-items: center; justify-content: center; text-align: center;
    color: #fff; font-size: 15px; line-height: 20px; padding: 10px;
  }

  .back-name {
    position: absolute; left: 0; right: 0; top: 160px; text-align: center;
    color: #fff; font-size: 40px; letter-spacing: 1px;
  }
  .back-url {
    position: absolute; left: 0; right: 0; top: 356px; text-align: center;
    color: #fff; font-size: 19px; letter-spacing: 3px;
  }
  .back-url strong { font-weight: 700; }
</style>
</head>
<body>
<main class="stage">
  <section class="card card-front">
    <svg class="front-waves" viewBox="0 0 730 417" width="730" height="417" aria-hidden="true">
      <defs>
        <linearGradient id="blueBand" x1="0" y1="0" x2="1" y2="0">
          <stop offset="0" stop-color="#143f68"/>
          <stop offset="0.55" stop-color="#1d8fd0"/>
          <stop offset="1" stop-color="#143f68"/>
        </linearGradient>
        <linearGradient id="orangeBand" x1="0" y1="0" x2="1" y2="0">
          <stop offset="0" stop-color="#f08a1e"/>
          <stop offset="1" stop-color="#f6a23a"/>
        </linearGradient>
      </defs>
      <path d="M0,380 C160,425 360,405 500,305 C585,245 650,205 730,195 L730,417 L0,417 Z" fill="url(#blueBand)"/>
      <path d="M0,320 C130,380 310,395 455,318 C560,258 640,195 730,180 L730,190 C645,205 565,270 470,332 C325,420 140,405 0,350 Z" fill="url(#orangeBand)"/>
      <path d="M60,340 C200,385 330,380 420,345 C330,395 190,395 60,340 Z" fill="#f6a23a"/>
    </svg>

    <h1 class="program-name">MoneyMendPlus</h1>
    <p class="slogan">Happiness, Restored!</p>
    <address class="address" style="font-style:normal">30871 Calloway Ln. B-22<br>Houston, TX 75419</address>

    <ul class="contact">
      <li><svg viewBox="0 0 16 16"><path d="M3 1l3 3-2 2c1 2 3 4 5 5l2-2 3 3-2 3C7 15 1 9 1 3z"/></svg>555-318-6207</li>
      <li><svg viewBox="0 0 16 16"><path d="M3 6h10v7H3zM5 2h6v3H5zM5 9h6v1H5z"/></svg>555-294-7153</li>
      <li><svg viewBox="0 0 16 16"><path d="M1 4h14v9H1zM1 4l7 5 7-5" stroke="#143f68" stroke-width="1"/></svg>info@miravelllending.example</li>
      <li><svg viewBox="0 0 16 16"><circle cx="8" cy="8" r="6.5" fill="none" stroke="#fff" stroke-width="1.4"/><path d="M1.5 8h13M8 1.5c-3 3-3 10 0 13M8 1.5c3 3 3 10 0 13" fill="none" stroke="#fff" stroke-width="1.2"/></svg>www.miravelllending.example</li>
    </ul>

    <div class="company-badge">Mira Vell Lending</div>
  </section>

  <section class="card card-back">
    <p class="back-name">Mira Vell Lending</p>
    <p class="back-url">www.<strong>miravelllending</strong>.example</p>
  </section>
</main>
</body>
</html>
```